Tradlo - Forex Signal Services Moments Matter Most. Reshape your path.

I need an attractive eye catching web design that is azure friendly. I currently have a web programmer working on the backend of my website. Now I need a professional design to attract and retain customers. This site needs to be mobile friendly.

Tradlo is a highly reputable, trustworthy and professional site that offers forex signals to traders in all parts of the globe. With accurate and reliable forex signals, traders can not only make money but also boost their profits.

At Tradlo, we want our clients to have complete faith on us and our services! We also do not want our users to lead a simple and monotonous life. Instead our goal is to help them create an extra source of steady income. However, this is possible only when our clients resolve to change their lives for the better. They need to change their mindset and most importantly develop a positive frame of mind. That’s exactly why at Tradlo, we provide our clients with innumerable personal development tools and resources that’ll aid them in changing all the aspects of their lives. We want our traders to feel inspired and educate them in the right way!

Colors are flexible.

I do like the simplicity of www.brightmarkvo.example.
I do want a design more professional in appearance and not everything on page one.

I have not been able to decide on a logo. There is one of lower quality as I have not paid for it yet but I will if you decide it's the best for my business I will. Or should one feel that they have a better idea for a logo, I will pay for it if i like it.

I have included some of the content of my site so you can get a feel for where I am coming from.
(Please note that this content is still in the editing process)
Updates

Project Deadline Extended Reason: My content was not complete nor finalization of the final logo. We will allow a few more days for designers to modify the website.Thank you for your patience and understanding. Added Tuesday, January 24, 2017

Target Market(s)

I work with Forex Traders, Investors wanting to control their own portfolios, and remote nomads/mellienials

Coding

Coded - Design and coding required

Number of Pages Required

5+ page

Requirements
Must have
• I must have a professional clean look. I want the site to be interactive and eye catching. I want my audience hooked within seconds of opening it. It has to have all important information first. Photos must be legit and not spammy. I work as a representative in the financial market. I want my site to reflect that I stand by my product and reputation means everything to me. This site has to be engaging.
• Sorry, I should have included this earlier of what I will all need on this site.
• I'll have about Tradlo (my company, what we stand for, who we work with, my strategy, etc....
• about me (why i started this company, who I am)
• Performance (graphs and recent posts of signals)
• Membership (how to sign up)
• Terms of service/legal/disclaimers
• FAQS
• Personal Development Resources
• Forex Education Resources
Nice to have
• Quick links to bounce around the site faster.
Should not have
• I do not want over the top white collar conservative.

```html
<!DOCTYPE html>
<html lang="en">
<head>
<meta charset="utf-8">
<title>Tradlo - Forex Signal Services</title>
<link href="https://fonts.googleapis.com/css2?family=Open+Sans:wght@400;600;700;800&display=swap" rel="stylesheet">
<style>
:root{
  --ink:#2b2f33;
  --muted:#6b7177;
  --line:#d9dcdf;
  --soft:#f1f2f3;
  --dark:#1b2127;
  --darker:#12171c;
  --lime:#9bc53d;
  --blue:#1a8fd0;
  --sky:#1ea3e0;
  --navy:#0f2a5e;
  --steel:#4b5761;
  --accent:#3d7fa6;
  --white:#ffffff;
}
*{box-sizing:border-box;margin:0;padding:0}
html,body{width:1200px;height:4500px;overflow:hidden}
body{font-family:"Open Sans",Arial,sans-serif;color:var(--ink);background:var(--white);position:relative}
section,header,footer{position:relative;width:1200px;overflow:hidden}

/* header */
.site-header{height:690px}
.hero-photo{position:absolute;inset:0;background:radial-gradient(ellipse at 78% 45%,#2c6fa6 0%,#173a5c 35%,#0d1c2b 70%,#0a121a 100%)}
.utility-bar{position:absolute;top:0;right:30px;height:36px;display:flex;align-items:center;gap:18px;color:var(--white);font-size:13px;font-weight:600}
.utility-item{display:flex;align-items:center;gap:6px}
.social-dot{width:18px;height:18px;border-radius:50%;background:#d5d9dd}
.main-nav{position:absolute;top:36px;left:0;right:0;height:66px;display:flex;align-items:center;justify-content:space-between;padding:0 30px 0 40px}
.brand{display:flex;align-items:center;gap:10px;font-size:40px;font-weight:800;color:var(--lime);letter-spacing:1px}
.brand-dot{width:16px;height:16px;border-radius:50%;background:var(--lime)}
.nav-links{display:flex;list-style:none;font-size:13px;font-weight:700;color:var(--white)}
.nav-links li{padding:0 14px;height:66px;display:flex;align-items:center}
.nav-links li.is-active{background:rgba(255,255,255,.18)}
.hero-slogan{position:absolute;top:280px;left:100px;color:var(--white);font-size:40px;font-weight:800;line-height:1.15;text-transform:uppercase;text-shadow:0 2px 6px rgba(0,0,0,.5)}
.welcome-band{position:absolute;left:0;right:0;top:495px;height:195px;background:rgba(236,238,240,.9);padding:36px 75px 0}
.welcome-band h1{font-size:44px;font-weight:800;color:var(--ink);line-height:1}
.welcome-band p{margin-top:14px;font-size:15px;line-height:1.5;color:var(--ink);max-width:1050px}

/* section headings */
.section-title{display:flex;align-items:center;justify-content:center;gap:22px;font-size:22px;font-weight:800;text-transform:uppercase;color:var(--ink)}
.section-title::before,.section-title::after{content:"";width:110px;height:1px;background:var(--line)}
.section-title span{color:var(--accent)}
.on-dark .section-title{color:var(--white)}
.on-dark .section-title::before,.on-dark .section-title::after{background:rgba(255,255,255,.35)}

/* what we do */
.what-we-do{height:495px;padding-top:60px}
.service-list{display:flex;justify-content:center;gap:20px;margin-top:55px;padding:0 100px}
.service{width:230px;text-align:center}
.service-icon{width:92px;height:92px;border-radius:50%;background:#4f5963;margin:0 auto 18px;display:flex;align-items:center;justify-content:center;box-shadow:0 0 0 5px #e3e6e8}
.service h3{font-size:15px;font-weight:700}
.service p{margin-top:6px;font-size:13px;line-height:1.5;color:var(--muted)}

/* strategy */
.strategy{height:470px;background:var(--soft);padding-top:80px}
.strategy-text{margin:40px 90px 0;font-size:14px;line-height:1.65;color:var(--ink)}
.strategy-text p+p{margin-top:14px}
.btn-dark{display:block;width:310px;margin:34px auto 0;background:var(--steel);color:var(--white);font-size:15px;font-weight:700;text-align:center;padding:12px 0;border-radius:5px}

/* why */
.why{height:560px;padding-top:70px}
.why-photo{position:absolute;inset:0;background:radial-gradient(ellipse at 50% 55%,#3a4147 0%,#22282d 55%,#111519 100%)}
.why .section-title{position:relative}
.why-diagram{position:absolute;left:350px;top:125px}
.why-point{position:absolute;width:260px;font-size:14px;font-weight:700;line-height:1.35;color:var(--white)}
.why-point.left{text-align:right}

/* performance */
.performance{height:590px;padding-top:60px}
.year-select{width:240px;height:40px;margin:35px auto 0;border:1px solid #b9bec3;border-radius:4px;display:flex;align-items:center;justify-content:center;gap:70px;font-size:15px;font-weight:700;background:linear-gradient(#fff,#eceef0)}
.pips-table{width:930px;margin:40px auto 0;border-collapse:collapse;font-size:15px;font-weight:700;border:1px solid var(--line)}
.pips-table th{background:var(--steel);color:var(--white);height:40px}
.pips-table td{height:44px;border:1px solid var(--line);text-align:center}
.pips-table tr:nth-child(even) td{background:#eef0f2}
.pips-table col.month{width:175px}

/* membership */
.membership{height:595px;padding-top:55px}
.membership-photo{position:absolute;inset:0;background:linear-gradient(135deg,#0c1c2e 0%,#12273d 45%,#0a1420 100%)}
.plan-list{position:relative;display:flex;justify-content:center;gap:30px;margin-top:40px}
.plan{width:280px;height:430px;border:2px solid var(--blue);background:#0a0f14;text-align:center;color:var(--white)}
.plan-price{font-size:58px;font-weight:800;font-style:italic;padding-top:30px;line-height:1}
.plan-term{font-size:13px;font-weight:700;margin:22px 0 18px}
.plan-features{list-style:none;margin:0 14px}
.plan-features li{font-size:13px;color:#c5cacf;background:#1f262d;border-top:1px solid #333b43;padding:8px 0}
.plan-features li:nth-child(even){background:#161c22}
.btn-order{display:block;margin:24px 26px 0;background:var(--blue);font-size:16px;font-weight:800;padding:9px 0}

/* faq */
.faq{height:335px;padding-top:32px}
.faq-columns{display:flex;gap:120px;margin:42px 0 0 144px}
.faq-list{list-style:none;width:420px}
.faq-list li{font-size:14px;font-weight:700;padding:10px 0;border-bottom:1px solid var(--line)}
.faq-list li::before{content:"+ ";color:var(--ink)}

/* contact */
.contact{height:415px;padding-top:55px}
.contact .section-title::before,.contact .section-title::after{width:70px}
.message-form{position:absolute;left:75px;top:55px;width:645px}
.field-grid{display:grid;grid-template-columns:1fr 1fr;gap:18px 15px;margin-top:35px}
.field{height:45px;border:1px solid #bfc4c9;border-radius:4px;padding:12px 14px;font-size:14px;font-weight:600}
.field.message{grid-column:1/3;height:105px}
.contact-info{position:absolute;left:850px;top:55px;width:300px}
.info-rows{margin-top:35px}
.info-row{display:flex;gap:16px;align-items:flex-start;font-size:14px;line-height:1.45;margin-bottom:20px}
.info-icon{width:28px;height:28px;border-radius:50%;background:var(--blue);flex:none;display:flex;align-items:center;justify-content:center}

/* trial */
.trial-banner{height:140px;background:var(--sky);display:flex;align-items:center;padding:0 105px 0 80px}
.trial-badge{width:96px;height:96px;border-radius:50%;border:3px solid var(--white);color:var(--white);display:flex;flex-direction:column;align-items:center;justify-content:center;font-weight:800;line-height:1}
.trial-badge b{font-size:34px}
.trial-badge small{font-size:11px;margin-top:4px}
.trial-text{margin-left:30px;color:var(--white);font-size:24px;font-weight:700;flex:1}
.btn-trial{background:var(--navy);color:var(--white);font-size:18px;font-weight:800;padding:16px 30px}

/* footer */
.site-footer{height:210px;padding:36px 45px 0}
.copyright{font-size:12px;font-weight:600}
.disclaimer{margin-top:28px;font-size:11px;line-height:1.6;color:var(--muted)}
</style>
</head>
<body>

<header class="site-header">
  <div class="hero-photo" role="img" aria-label="Photo of a trader's hand near a desktop monitor showing blue market data"></div>
  <div class="utility-bar">
    <span class="utility-item">
      <svg width="16" height="16" viewBox="0 0 16 16"><circle cx="8" cy="8" r="8" fill="#fff"/><path d="M5 4l2 2-1 1.2c.6 1.2 1.6 2.2 2.8 2.8L10 9l2 2-1.3 1.3C7.5 12 4 8.5 3.7 5.3z" fill="#1b2127"/></svg>
      800.555.0142
    </span>
    <span class="utility-item">
      <svg width="16" height="16" viewBox="0 0 16 16"><circle cx="8" cy="8" r="8" fill="#fff"/><rect x="4" y="5" width="8" height="6" fill="none" stroke="#1b2127"/><path d="M4 5l4 3 4-3" fill="none" stroke="#1b2127"/></svg>
      info@tradlo.example
    </span>
    <span class="social-dot"></span><span class="social-dot"></span><span class="social-dot"></span>
  </div>
  <nav class="main-nav">
    <div class="brand"><span class="brand-dot"></span>Tradlo</div>
    <ul class="nav-links">
      <li class="is-active">HOME</li><li>MY COMPANY ▾</li><li>ABOUT</li><li>PERFORMANCE</li><li>MEMBERSHIP</li><li>FAQ</li><li>RESOURCES ▾</li><li>CONTACT</li>
    </ul>
  </nav>
  <p class="hero-slogan">Moments Matter Most.<br>Reshape your path.</p>
  <div class="welcome-band">
    <h1>WELCOME TO TRADLO</h1>
    <p>We use proven strategies to help traders in succeeding in the forex market. Our forex experts provide high-probability, professional and consistent forex signals and charts that help traders in maximizing their profits and eliminating losses.</p>
  </div>
</header>

<section class="what-we-do">
  <h2 class="section-title">What <span>We Do</span></h2>
  <div class="service-list">
    <div class="service">
      <div class="service-icon"><svg width="50" height="50" viewBox="0 0 50 50" fill="none" stroke="#fff" stroke-width="2"><circle cx="17" cy="17" r="11"/><circle cx="33" cy="33" r="11"/><text x="17" y="22" fill="#fff" stroke="none" font-size="13" text-anchor="middle" font-family="Open Sans,sans-serif">$</text><text x="33" y="38" fill="#fff" stroke="none" font-size="13" text-anchor="middle" font-family="Open Sans,sans-serif">€</text></svg></div>
      <h3>We Choose the Best Forex Pair</h3>
      <p>We use the only the best – 5 currency pairs.</p>
    </div>
    <div class="service">
      <div class="service-icon"><svg width="50" height="50" viewBox="0 0 50 50" fill="none" stroke="#fff" stroke-width="2"><rect x="8" y="10" width="34" height="26"/><path d="M12 30l8-8 6 5 12-12"/><path d="M20 42h10M25 36v6"/></svg></div>
      <h3>Analyze the Forex Chart</h3>
      <p>The strategy is used to analyze all 5 chosen currency pair charts and the most profitable entry point is identified and sent to subscribers.</p>
    </div>
    <div class="service">
      <div class="service-icon"><svg width="50" height="50" viewBox="0 0 50 50" fill="none" stroke="#fff" stroke-width="2"><rect x="10" y="14" width="22" height="26" rx="2"/><path d="M22 24h18M34 18l6 6-6 6"/></svg></div>
      <h3>Send Forex Signals</h3>
      <p>Signals are sent to our Subscribers through SMS, Members Area, Email and App push notification.</p>
    </div>
    <div class="service">
      <div class="service-icon"><svg width="50" height="50" viewBox="0 0 50 50" fill="none" stroke="#fff" stroke-width="2"><path d="M18 12h14l-4 7c8 4 12 10 12 16 0 4-3 6-7 6H17c-4 0-7-2-7-6 0-6 4-12 12-16z"/><text x="25" y="37" fill="#fff" stroke="none" font-size="13" text-anchor="middle" font-family="Open Sans,sans-serif">$</text></svg></div>
      <h3>You Make Money</h3>
      <p>150-250+ pips per month! A maximum of 15 to 30 signals is sent per month. Expect to make 20-50 pips per signal.</p>
    </div>
  </div>
</section>

<section class="strategy">
  <h2 class="section-title">Our <span>Strategy</span></h2>
  <div class="strategy-text">
    <p>Tradlo.example works with both day as well as intraday traders. We only hold a maximum of one position at any given point in time. Once we've placed an order we do not move SL or TP targets.</p>
    <p>We follow naked forex trading techniques including price action, immediate trend and personalized mathematical formulas. Our success stems from our strict enforcement of discipline, patience, attitude, economics and timing to help our traders maximize their gains from forex trading. At Tradlo, we trade GBP/USD, EUR/USD, AUD/USD, USD/CHF and USD/JPY pairs only and target anywhere between 25-50 pips a day with a risk/reward ratio of at least 2:1.</p>
    <p>Our maximum drawdown is 18% and we strive to average 150-250 pips per month. We strongly recommend no more than 3% leveraged risk of your account for any trade. Most trades are closed within hours.</p>
  </div>
  <span class="btn-dark">Learn More About Forex Basics!</span>
</section>

<section class="why on-dark">
  <div class="why-photo" role="img" aria-label="Dark blurred photo of a trading desk"></div>
  <h2 class="section-title">Why Tradlo</h2>
  <svg class="why-diagram" width="500" height="420" viewBox="0 0 500 420">
    <circle cx="250" cy="210" r="190" fill="none" stroke="rgba(255,255,255,.5)" stroke-width="2"/>
    <circle cx="250" cy="210" r="140" fill="#2a3137" stroke="rgba(255,255,255,.25)" stroke-width="6"/>
    <circle cx="250" cy="210" r="10" fill="#9bc53d" transform="translate(-80 0)"/>
    <text x="262" y="224" fill="#9bc53d" font-family="Open Sans,sans-serif" font-size="44" font-weight="800" text-anchor="middle">Tradlo</text>
    <g fill="#fff" stroke="#2a3137" stroke-width="3">
      <circle cx="155" cy="45" r="28"/><circle cx="345" cy="45" r="28"/>
      <circle cx="75" cy="140" r="28"/><circle cx="425" cy="140" r="28"/>
      <circle cx="75" cy="280" r="28"/><circle cx="425" cy="280" r="28"/>
      <circle cx="155" cy="375" r="28"/><circle cx="345" cy="375" r="28"/>
    </g>
    <g fill="none" stroke="#2a3137" stroke-width="2.5" stroke-linecap="round">
      <path d="M142 55l9-9 6 5 11-12"/>
      <path d="M333 45h24M345 33v24"/>
      <path d="M63 140l8 8 16-16"/>
      <path d="M413 140h20M427 132l8 8-8 8"/>
      <path d="M63 280h18M75 272l8 8-8 8"/>
      <path d="M413 272h24M413 280h24M413 288h24"/>
      <path d="M144 385v-10M153 385v-16M162 385v-8M170 385v-20"/>
      <circle cx="345" cy="375" r="9"/>
    </g>
  </svg>
  <p class="why-point left" style="left:150px;top:160px">Our motto is to 'Change Your World' and also to ensure that you earn profits on a regular basis.</p>
  <p class="why-point left" style="left:110px;top:255px">We're a highly dependable and trusted forex trading platform.</p>
  <p class="why-point left" style="left:110px;top:385px">We offer speedy, consistent, accurate and desired results.</p>
  <p class="why-point left" style="left:150px;top:465px">Our team will constantly update you regarding the status of your trade till the time it is closed.</p>
  <p class="why-point" style="left:790px;top:160px">Our objective is to provide global access to trusted forex signals.</p>
  <p class="why-point" style="left:830px;top:255px">Our services are highly affordable.</p>
  <p class="why-point" style="left:830px;top:385px">We offer High Probable forex strategies with high rewards.</p>
  <p class="why-point" style="left:790px;top:475px">We set transparent entry price and exit levels.</p>
</section>

<section class="performance">
  <h2 class="section-title">Performance</h2>
  <div class="year-select"><span>2017</span><span>▾</span></div>
  <table class="pips-table">
    <colgroup><col class="month"><col><col class="month"><col></colgroup>
    <tr><th>Month</th><th>PIPS</th><th>Month</th><th>PIPS</th></tr>
    <tr><td>January</td><td></td><td>July</td><td></td></tr>
    <tr><td>February</td><td></td><td>August</td><td></td></tr>
    <tr><td>March</td><td></td><td>September</td><td></td></tr>
    <tr><td>April</td><td></td><td>October</td><td></td></tr>
    <tr><td>May</td><td></td><td>November</td><td></td></tr>
    <tr><td>June</td><td></td><td>December</td><td></td></tr>
  </table>
</section>

<section class="membership on-dark">
  <div class="membership-photo" role="img" aria-label="Dark blue photo of city lights at night"></div>
  <h2 class="section-title" style="position:relative">Membership</h2>
  <div class="plan-list">
    <div class="plan">
      <div class="plan-price">$ 69</div><div class="plan-term">1 MONTH</div>
      <ul class="plan-features"><li>Lorem Ipsum</li><li>Dolor sit amet</li><li>Adipiscing elit</li><li>Euismod tincidunt</li><li>Duis autem vel eum iriure</li></ul>
      <span class="btn-order">ORDER NOW</span>
    </div>
    <div class="plan">
      <div class="plan-price">$ 139</div><div class="plan-term">3 MONTHS</div>
      <ul class="plan-features"><li>Lorem Ipsum</li><li>Dolor sit amet</li><li>Adipiscing elit</li><li>Euismod tincidunt</li><li>Duis autem vel eum iriure</li></ul>
      <span class="btn-order">ORDER NOW</span>
    </div>
    <div class="plan">
      <div class="plan-price">$ 549</div><div class="plan-term">12 MONTHS</div>
      <ul class="plan-features"><li>Lorem Ipsum</li><li>Dolor sit amet</li><li>Adipiscing elit</li><li>Euismod tincidunt</li><li>Duis autem vel eum iriure</li></ul>
      <span class="btn-order">ORDER NOW</span>
    </div>
  </div>
</section>

<section class="faq">
  <h2 class="section-title">Frequently Asked <span>Questions</span></h2>
  <div class="faq-columns">
    <ul class="faq-list">
      <li>Why Tradlo?</li>
      <li>What is your trading philosophy and style?</li>
      <li>How many signals do you send out per month?</li>
      <li>How many pips can I make per month following your signals?</li>
    </ul>
    <ul class="faq-list">
      <li>Can I follow your signals if I have a full-time job?</li>
      <li>How will I know when a new signal is released?</li>
      <li>How do I subscribe to your service?</li>
      <li>What happens after my 30-day free trial access?</li>
    </ul>
  </div>
</section>

<section class="contact">
  <div class="message-form">
    <h2 class="section-title">Send a <span>Message</span></h2>
    <div class="field-grid">
      <div class="field">Name</div><div class="field">Email Address</div>
      <div class="field">Phone Number</div><div class="field">Company</div>
      <div class="field message">Message</div>
    </div>
  </div>
  <div class="contact-info">
    <h2 class="section-title">Contact <span>Info</span></h2>
    <div class="info-rows">
      <div class="info-row"><span class="info-icon"><svg width="14" height="14" viewBox="0 0 14 14"><path d="M7 1a4 4 0 0 0-4 4c0 3 4 8 4 8s4-5 4-8a4 4 0 0 0-4-4z" fill="#fff"/></svg></span><span>TRADLO<br>1234 Lorem Ipsum Dr<br>Ste 200<br>Ridgefall, Alberta</span></div>
      <div class="info-row"><span class="info-icon"><svg width="14" height="14" viewBox="0 0 14 14"><path d="M3 2l2.5 2.5-1.2 1.4c.7 1.5 1.8 2.6 3.3 3.3l1.4-1.2L11.5 10.5 10 12C6 11.5 2.5 8 2 4z" fill="#fff"/></svg></span><span>(800) 555-0142</span></div>
      <div class="info-row"><span class="info-icon"><svg width="14" height="14" viewBox="0 0 14 14"><rect x="2" y="3.5" width="10" height="7" fill="none" stroke="#fff"/><path d="M2 3.5l5 4 5-4" fill="none" stroke="#fff"/></svg></span><span>info@tradlo.example</span></div>
    </div>
  </div>
</section>

<section class="trial-banner">
  <div class="trial-badge"><b>30</b><small>FREE TRIAL</small></div>
  <p class="trial-text">Free forex signals for 30 days. Start your trial right now.</p>
  <span class="btn-trial">START FREE TRIAL</span>
</section>

<footer class="site-footer">
  <p class="copyright">© 2017 TRADLO | All rights reserved.</p>
  <p class="disclaimer">Disclaimer: Trading foreign exchange on margin carries a high level of risk and may not be suitable for all investors. Before deciding to trade forex you should carefully consider your investment objectives, level of experience and appetite for risk. Only trade with money you are prepared to lose. The possibility exists that you could sustain a loss in excess of your initial deposit, therefore you should not speculate with capital that you cannot afford to lose. Past performance is not an indicator of future returns, and results shown on this site are provided as historical benchmarks only. Tradlo does not take responsibility for losses incurred as a result of our trading signals. By signing up as a member you acknowledge that we are not providing financial advice and that you are making the decision to use our trades on your own account. All information is for educational purposes only.</p>
</footer>

</body>
</html>
```